Brisk. Technology Logistics Software platform.

A modern looking and feeling website for a logistics software platform.
We connect retailers or wholesale parcel distributors to worldwide delivery solutions.
Methods tend to be road and air transport to final mile courier companies and post offices all over the world.
Our platform is for ecommerce distribution. A customer uses BRISK to enable them to connect to worldwide companies who will track and trace the delivery of their goods.

Target Market(s)

Onllne retailers. Markert Places such as Vendora and Tradelo. Wholesale third party logistics and packaging companies. Delivery companies based in the UK looking to expand overseas.

Number of Pages Required

5+ page

Font styles to use
Sans Serif

Colors
aaaaaa
dbdbdb
e6e6e6
c4c4c4
cbcbcb
c9c9c9
ec1f27
3176b5
0355a3

Requirements
Must have
• Landing Page.
• What we do.
• Who we are.
• Modules.
• Testimonies (password protected)
• Contact us.
• Interactive for mobile operating systems.
• Scrolling website.
• Short stock video showing on key pages.
• Very well polished fonts and buttons. A sharp and well executed website is required.
• Simplicity in feeling.
• To the point on message.
• Refined wording and copyrighting / messaging
• A link to our sub brand and product Brisk Parcels
• Capture interest so people read further.
Nice to have
• A polished video to explain what we do on landing page. Clipmarrow.net have some good options but not sure how professional they will look.
Should not have
• Bad graphics and colours.
• Not lots of clicks. Less as possible
• Complex message

```html
<!DOCTYPE html>
<html lang="en">
<head>
<meta charset="utf-8">
<title>Brisk. Technology – Website Screens</title>
<link href="https://fonts.googleapis.com/css2?family=Poppins:wght@400;500;600&display=swap" rel="stylesheet">
<style>
  :root {
    --brand-red: #ec1f27;
    --ink: #222222;
    --body-grey: #555555;
    --nav-grey: #444444;
    --paper: #ffffff;
    --warehouse-dark: #2c2f3a;
    --warehouse-mid: #4a4f5e;
    --yard-dark: #3a3d40;
    --yard-mid: #5b6064;
  }
  * { box-sizing: border-box; margin: 0; padding: 0; }
  html, body { width: 1200px; height: 624px; overflow: hidden; background: var(--paper); }
  body { font-family: "Poppins", sans-serif; position: relative; }

  .screen {
    position: absolute; top: 53px; width: 540px;
    background: var(--paper);
    box-shadow: 0 1px 8px rgba(0,0,0,0.18);
    overflow: hidden;
  }
  .screen--mobile-menu { left: 52px; height: 338px; }
  .screen--desktop { left: 608px; height: 512px; }

  .site-header { height: 39px; position: relative; background: var(--paper); }
  .brand {
    position: absolute; left: 52px; top: 10px;
    display: flex; align-items: center; gap: 4px;
    font-weight: 600; font-size: 15px; color: var(--brand-red); line-height: 1;
    letter-spacing: -0.2px;
  }
  .brand-dot { width: 9px; height: 9px; border-radius: 50%; background: var(--brand-red); }
  .brand-sub { display: block; font-size: 7px; letter-spacing: 0.4px; margin-top: 1px; }
  .menu-toggle {
    position: absolute; right: 56px; top: 12px; width: 15px; height: 15px;
    border-radius: 50%; background: #111;
  }
  .main-nav {
    position: absolute; left: 293px; top: 14px; display: flex; gap: 15px;
    font-size: 8px; color: var(--nav-grey);
  }

  .hero { position: relative; height: 251px; color: #fff; text-align: center; }
  .hero-media { position: absolute; inset: 0; }
  .hero-media--warehouse { background: linear-gradient(160deg, var(--warehouse-mid), var(--warehouse-dark) 70%, #3b3a2c); }
  .hero-media--yard { background: linear-gradient(140deg, #3f5570, var(--yard-mid) 40%, var(--yard-dark) 75%, #5e5430); }
  .hero-content { position: absolute; left: 0; right: 0; }
  .play-button { position: absolute; left: 254px; top: 63px; }
  .hero-title { font-weight: 500; font-size: 17px; line-height: 1; }
  .hero-copy { font-size: 8px; line-height: 11.7px; width: 300px; margin: 0 auto; }
  .hero-sub { font-size: 8px; font-weight: 500; }

  .slide-dots { position: absolute; right: 39px; top: 111px; display: flex; flex-direction: column; align-items: center; gap: 4px; }
  .slide-dot { width: 4px; height: 4px; border-radius: 50%; background: #fff; }
  .slide-dot--active { width: 9px; height: 9px; border: 1.5px solid #fff; background: transparent; position: relative; }
  .slide-dot--active::after { content: ""; position: absolute; inset: 1.5px; border-radius: 50%; background: #fff; }

  .intro { height: 174px; text-align: center; color: var(--body-grey); font-size: 8.2px; line-height: 13.8px; padding-top: 18px; }
  .intro p { width: 380px; margin: 0 auto; }
  .intro .intro-note { margin-top: 10px; }
  .cta-row { display: flex; justify-content: center; gap: 16px; margin-top: 15px; }
  .cta {
    height: 26px; background: var(--brand-red); color: #fff; font-size: 9px;
    display: flex; align-items: center; justify-content: center; text-decoration: none;
  }
  .cta--parcel { width: 96px; }
  .cta--tech { width: 106px; }

  .site-footer { height: 48px; background: var(--brand-red); color: #fff; text-align: center; position: relative; }
  .social { position: absolute; top: 11px; left: 0; right: 0; display: flex; justify-content: center; gap: 4px; }
  .social-link { width: 14px; height: 14px; border: 1px solid #fff; border-radius: 50%; }
  .copyright { position: absolute; top: 32px; left: 0; right: 0; font-size: 6px; }
</style>
</head>
<body>

  <section class="screen screen--mobile-menu">
    <header class="site-header">
      <div class="brand"><span class="brand-dot"></span><span>Brisk.<span class="brand-sub">Technology</span></span></div>
      <span class="menu-toggle" aria-label="Menu"></span>
    </header>
    <div class="hero">
      <div class="hero-media hero-media--warehouse" role="img" aria-label="Video still of a warehouse with tall racking, stacked boxes and a forklift"></div>
      <svg class="play-button" width="32" height="32" viewBox="0 0 32 32" aria-label="Play video">
        <circle cx="16" cy="16" r="15" fill="none" stroke="#fff" stroke-width="1.3"/>
        <path d="M12.5 9.5 L22 16 L12.5 22.5 Z" fill="none" stroke="#fff" stroke-width="1.3" stroke-linejoin="round"/>
      </svg>
      <div class="hero-content" style="top:100px">
        <h1 class="hero-title">Brisk.Technology … Our Focus</h1>
      </div>
      <div class="hero-content" style="top:125px">
        <p class="hero-copy">We Provide Advanced Software Solutions To Ensure You Connect With Global ECommerce Delivery CarriersYou Can Manage Your Global Delivery Network In One Place, With Our Software Will Enable You Monitor The Productivity And Reporting Of Your ECommerce Deliveries Manage Your Carriers, Your Delivery Speeds, And Your Costs</p>
      </div>
      <div class="slide-dots"><span class="slide-dot slide-dot--active"></span><span class="slide-dot"></span><span class="slide-dot"></span></div>
    </div>
    <footer class="site-footer">
      <div class="social"><span class="social-link" aria-label="Social link"></span><span class="social-link" aria-label="Social link"></span><span class="social-link" aria-label="Social link"></span></div>
      <p class="copyright">Copyright 2018 | All Rights Reserved | Privacy Policy | Term &amp; Conditions</p>
    </footer>
  </section>

  <section class="screen screen--desktop">
    <header class="site-header">
      <div class="brand"><span class="brand-dot"></span><span>Brisk.<span class="brand-sub">Technology</span></span></div>
      <nav class="main-nav"><span>Home</span><span>Solutions</span><span>Testimonials</span><span>Contact Us</span></nav>
    </header>
    <div class="hero">
      <div class="hero-media hero-media--yard" role="img" aria-label="Aerial video still of a distribution centre with trucks at loading bays"></div>
      <div class="hero-content" style="top:106px">
        <h1 class="hero-title" style="font-size:18px">Brisk. Technology &amp; Parcel Solutions</h1>
      </div>
      <div class="hero-content" style="top:134px">
        <p class="hero-sub">Built To Help Develop &amp; Manage Your Global Delivery Network</p>
      </div>
      <div class="slide-dots"><span class="slide-dot slide-dot--active"></span><span class="slide-dot"></span><span class="slide-dot"></span></div>
    </div>
    <section class="intro">
      <p>Working closely with Ecommerce, Brisk. Technology have developed solutions purely focused on delivering what's required within the global delivery marketplace. Meeting all needs and more for Retailers and Global Delivery Solution providers.Allowing customers to grow at a fast pace; most importantly providing tools to help them manage their global delivery network supported by "Dynamic Real Time Visibility" management tools</p>
      <p class="intro-note">Ensuring solutions evolve to suit our customers business requirements</p>
      <div class="cta-row">
        <a class="cta cta--parcel" href="#">Brisk Parcel</a>
        <a class="cta cta--tech" href="#">Brisk Technology</a>
      </div>
    </section>
    <footer class="site-footer">
      <div class="social"><span class="social-link" aria-label="Social link"></span><span class="social-link" aria-label="Social link"></span><span class="social-link" aria-label="Social link"></span></div>
      <p class="copyright">Copyright 2018 | All Rights Reserved | Privacy Policy | Term &amp; Conditions</p>
    </footer>
  </section>

</body>
</html>
```